Update patient consent forms and contract

Objective
Redesign the existing patient contract information document to create a modern,contempory, and easy-to-understand experience for patients. The updated design should improve readability, accessibility, and overall presentation while maintaining compliance with healthcare and legal requirements.

Key Deliverables

Refreshed visual design and layout
Improved information hierarchy and readability
Modern typography and colour palette aligned with brand guidelines
Clear section headings and navigation
Print-ready and digital versions (PDF)

Include KEV Logo within patient KEV consent to treatment. Ideally this document should be portrait not landscape.
Updates

I would love a front page to be included in the document

```html
<!DOCTYPE html>
<html lang="en">
<head>
<meta charset="utf-8">
<title>Orthodontics Treatment – Patient Consent Booklet</title>
<link rel="stylesheet" href="https://fonts.googleapis.com/css2?family=Manrope:wght@300;400;500;600;700;800&display=swap">
<style>
:root{
  --board:#8aabd0;
  --paper:#ffffff;
  --ink:#1d1f2a;
  --body:#575a63;
  --accent:#1b9ad8;
  --numeral:#b8daf0;
  --muted:#a9a9a9;
  --rule:#9a9a9a;
  --partner:#5c5f66;
}
*{box-sizing:border-box;margin:0;padding:0}
html,body{width:1200px;height:1125px;overflow:hidden;background:var(--board)}
body{font-family:'Manrope',sans-serif;color:var(--body);position:relative}
.page{position:absolute;width:368px;height:521px;background:var(--paper);overflow:hidden}
.p1{left:36px;top:36px;background:linear-gradient(180deg,#f4f8fc 0%,#ffffff 40%,#e4effa 100%)}
.p2{left:416px;top:36px;background:linear-gradient(180deg,#f3f7fc 0%,#ffffff 30%,#ffffff 80%,#eef4fb 100%)}
.p3{left:796px;top:36px;background:linear-gradient(180deg,#f3f7fc 0%,#ffffff 30%,#ffffff 80%,#eef4fb 100%)}
.p4{left:36px;top:568px}
.p5{left:416px;top:568px}
.p6{left:796px;top:568px}
.abs{position:absolute}
.fill{position:absolute;border-radius:2px}

/* cover */
.brand{position:absolute;left:72px;top:52px;display:flex;align-items:center;gap:6px;font-size:20px;font-weight:600;color:var(--muted);letter-spacing:.2px;white-space:nowrap}
.brand-dot{width:12px;height:12px;border-radius:50%;background:var(--accent)}
.tagline{position:absolute;left:0;width:100%;top:138px;text-align:center;font-size:9.5px;line-height:12px;color:var(--ink)}
.cover-title{position:absolute;left:0;width:100%;top:206px;text-align:center;line-height:1}
.cover-title .t1{display:block;font-size:26px;font-weight:500;color:var(--ink)}
.cover-title .t2{display:block;font-size:42px;font-weight:600;color:var(--accent);margin-top:2px}
.tooth-hero{left:80px;top:286px;width:210px;height:235px;border-radius:90px 90px 20px 20px;background:radial-gradient(ellipse at 50% 35%,#9fd4f5 0%,#3d9fe0 50%,#cfe6f8 100%)}

/* text */
.h-main{font-size:12px;line-height:13.5px;font-weight:500;color:var(--ink)}
.h-main span{color:var(--accent);display:block}
.h-accent{font-size:11.5px;font-weight:500;color:var(--accent)}
p{font-size:7px;line-height:8.9px;color:var(--body);margin-bottom:5px}
p .hl{color:var(--accent)}
.sec-head{display:flex;align-items:baseline;gap:6px;margin-bottom:6px}
.num{font-size:22px;font-weight:300;color:var(--numeral);line-height:1;letter-spacing:-.5px}
.sec-title{font-size:9.5px;font-weight:500;color:var(--ink);line-height:11px}

/* partner mark */
.partner{left:189px;top:282px;display:flex;align-items:center;gap:7px;font-size:16px;font-weight:600;color:var(--partner)}
.partner-mark{width:18px;height:18px;background:var(--partner)}

/* form */
.form{left:189px;top:352px;width:165px;font-size:6.6px;color:var(--ink)}
.line-row{display:flex;align-items:flex-end;gap:3px;height:14px}
.line-row .rule{flex:1;border-bottom:.6px solid var(--rule);height:6px}
.form .full{border-bottom:.6px solid var(--rule);height:14px}
.form p{font-size:6.6px}

/* placeholders */
.wip{position:absolute;left:0;width:100%;text-align:center;font-weight:700;color:var(--muted);text-transform:uppercase}
.wip .big{font-size:42px;position:absolute;top:120px;left:0;width:100%}
.wip-lines{position:absolute;top:208px;left:0;width:100%;font-size:31px;line-height:39.5px;letter-spacing:.3px}
</style>
</head>
<body>

<section class="page p1">
  <div class="brand"><span class="brand-dot"></span>Belmora orthodontics</div>
  <div class="tagline">Wearing your retainers is the most important<br>part of your orthodontic journey.</div>
  <h1 class="cover-title"><span class="t1">Orthodontics</span><span class="t2">Treatment</span></h1>
  <div class="fill tooth-hero" role="img" aria-label="Translucent blue tooth splashing in water"></div>
</section>

<section class="page p2">
  <div class="abs" style="left:17px;top:29px;width:170px">
    <h2 class="h-main">Orthodontics<span>Treatment</span></h2>
    <p style="margin-top:9px">Orthodontic treatment promotes a <span class="hl">healthy smile, healthier teeth and gums and a better bite for normal chewing.</span></p>
    <p>Orthodontic treatment depends for much of its success on the understanding and co-operation of the patient. This form covers the usual material risks associated with Orthodontic treatment.</p>
    <p>You may ask your orthodontist to explain anything you do not understand.</p>
  </div>
  <div class="fill" style="left:211px;top:16px;width:136px;height:135px;background:radial-gradient(ellipse at 50% 55%,#e6e9ee 0%,#c9ced6 45%,#f6f8fb 75%)" role="img" aria-label="Silver tooth model with dental mirror and implant"></div>
  <div class="fill" style="left:17px;top:167px;width:146px;height:136px;background:linear-gradient(135deg,#2f5fb8 0%,#5b8fd6 45%,#c9a89a 70%,#3a6bc2 100%)" role="img" aria-label="Patient receiving dental treatment"></div>
  <div class="abs" style="left:17px;top:316px;width:142px">
    <h3 class="h-accent">Benefits</h3>
    <p style="margin-top:8px">Orthodontics plays an important role in <span class="hl">improving overall oral health</span> and achieving <span class="hl">balance and harmony</span> between the face and teeth for a beautiful, healthy smile, which may enhance one's self esteem.The correct bite of teeth with health muscles and jaw joints will provide optimal chewing function . Properly aligned teeth are easier to brush and so the tendancy to decay may be decreased, as may the likelihood of developing disease of the gums and supporting bone Correctly aligned teeth are less likely to experience abnormal wear. Because of the individual conditions present and the limitations of treatment imposed by the nature each specific benefit may not be attainable for every patient.</p>
  </div>
  <div class="abs" style="left:179px;top:163px;width:168px">
    <p>While recognizing he benefits of healthy teeth and a pleasing smile, you should also be aware that orthodontic treatment has <span class="hl">limitations and potential risks</span> and there may be <span class="hl">alternative treatment options</span>. You should clarify what is expected of you as a patient, or as the parent of a young patient, to achieve excellent results. Keep in mind that with orthodontic treatment, like other healing arts, results cannot be guaranteed.</p>
    <p>The unknown factor in any orthodontic correction is the response of the patient to the orthodontic treatment.<br>Should you have any questions please ask.</p>
    <h3 class="h-accent" style="margin-top:8px">Risks</h3>
    <p style="margin-top:6px;color:var(--ink)">All forms of medical and dental treatment including orthodontics, have some risk and limitations. Fortunately in orthodontics complications are infrequent and when they do occur they are usually of only minor consequence. Nevertheless, they should be considered when making the decision to undergo orthodontic treatment. The principal risks in orthodontic treatment pertain to:</p>
    <div class="sec-head" style="margin-top:9px"><span class="num">01.</span><span class="sec-title">Oral Hygiene</span></div>
    <p>and permanent markings (decalcification) on teeth can occur if orthodontic patients eat food containing excessive sugar or do not brush teeth frequently or properly. These same problems can occur without orthodontic treatment but the risk is greater to an individual wearing braces.</p>
    <p>It is imperative during orthodontic treatment that extra care be taken with oral hygiene and tooth brushing in particular.</p>
  </div>
</section>

<section class="page p3">
  <div class="fill" style="left:230px;top:13px;width:138px;height:115px;background:radial-gradient(ellipse at 55% 50%,#dfe4ea 0%,#eef2f6 50%,#f7f9fc 80%)" role="img" aria-label="Clear aligner trays"></div>
  <div class="abs" style="left:17px;top:32px;width:164px">
    <div class="sec-head"><span class="num">02.</span><span class="sec-title">Relapse</span></div>
    <p>Teeth may have a tendency to change their positions after treatment. The long term faithful wearing of retainers should reduce this tendency. Teeth can however, move at any time, whether or not they have had orthodontic treatment. This is especially true during the late teen period when active growth of the facial bones is coming to an end. Most vulnerable teeth are those at the front.</p>
  </div>
  <div class="abs" style="left:17px;top:137px;width:164px">
    <div class="sec-head"><span class="num">03.</span><span class="sec-title">Periodontal Health</span></div>
    <p>thodontic tooth movement if a condition already exists, and in some rare cases where a condition does not appear to exist. In general, orthodontic treatment lessens the possibility of tooth loss or gums infection due to misalignment of the teeth or jaws. Inflammation of the gums and loss of supporting bone can occur if bacterial plaque is not removed daily with good oral hygiene.</p>
  </div>
  <div class="abs" style="left:17px;top:256px;width:164px">
    <div class="sec-head"><span class="num">04.</span><span class="sec-title">Root Shortening</span></div>
    <p>In some patients the length of the roots of the teeth may be shortened during or thodontic treatment. Some patients are prone to this happening, some are not. It is nearly impossible to predict susceptibility. Usually this shortening does not have significant consequences, but on very rare occasions it may become a threat to the longevity of the teeth involved.</p>
  </div>
  <div class="abs" style="left:17px;top:364px;width:164px">
    <div class="sec-head"><span class="num">05.</span><span class="sec-title">Jaw Joints</span></div>
    <p>Occasionally patients may suffer pain or dysfunction in the jaw joints (T.M.J's). This may present as joint pain, headaches or ear problems. These problems may occur with or without orthodontic treatment. Any of the above noted symptoms should be reported to the orthodontist. Some patients are susceptible to T.M.J. problems and some are not. Numerous studies have shown that movement of the teeth during orthodontic treatment is unrelated to the onset of T.M.J problems. Just as for painful conditions in other joints discomfort in T.M.J's can last from a few days to several weeks or longer.</p>
  </div>
  <div class="abs" style="left:191px;top:135px;width:164px">
    <div class="sec-head"><span class="num">06.</span><span class="sec-title">Tooth Vitality</span></div>
    <p>Sometimes a tooth may have been traumatized by a previous accident or a tooth may be decayed or have large fillings which can cause damage to the nerve of the tooth. Orthodontic tooth movement in some cases aggravates this condition and in rare instances may lead to loss of tooth vitality and discolouration of the tooth requiring root canal treatment and other dental treatment to restore the colour of the tooth.</p>
  </div>
  <div class="abs" style="left:191px;top:253px;width:164px">
    <div class="sec-head"><span class="num">07.</span><span class="sec-title">Loose appliances<br>&amp; discomfort</span></div>
    <p>The gums, cheeks or lips may be scratched or irritated by newly placed appliances or by loose or broken appliances or by blows to the mouth. You will be given instruction or minimising these effects. Very rarely loose orthodontic appliances may be accidentally swallowed or aspirated. You should inform your orthodontist of any unusual symptoms, broken or loose appliances, as soon as they are noted.</p>
    <p>Usual post adjustment tenderness should be expected, and the period of tenderness or sensitivity varies with each patient and the procedure performed. (typical post adjustment tenderness may last 24 to 48 hours.)</p>
  </div>
  <div class="fill" style="left:218px;top:425px;width:97px;height:79px;border-radius:40px;background:radial-gradient(ellipse at 50% 50%,#e3e6ea 0%,#f2f4f7 60%,#ffffff 100%)" role="img" aria-label="Two white tooth models"></div>
</section>

<section class="page p4">
  <div class="abs" style="left:17px;top:30px;width:160px">
    <div class="sec-head"><span class="num">08.</span><span class="sec-title">Atypical Growth</span></div>
    <p>Insufficient, excessive or asymmetrical changes in the growth of the jaws may limit our ability to achieve the desired result. If growth becomes disproportionate during orthodontic management the treatment may be prolonged. Growth changes that occur after orthodontic treatment may alter the quality of treatment results and may require further orthodontic treatment. Some cases of atypical growth, the bite may change so much that oral surgery is required to achieve the best possible result.</p>
  </div>
  <div class="abs" style="left:17px;top:165px;width:160px">
    <div class="sec-head"><span class="num">09.</span><span class="sec-title">Headgear</span></div>
    <p>If improperly handled, headgear may cause injury to the face. Patients are warned not to wear the appliance during the times of boisterous or competitive activity.</p>
  </div>
  <div class="abs" style="left:17px;top:240px;width:160px">
    <div class="sec-head"><span class="num">10.</span><span class="sec-title">Treatment Time</span></div>
    <p>The total time required to complete treatment may exceed the estimate. Poor co-operation in wearing the appliance or elastics the required hours per day, poor oral hygiene, broken appliances and missed appointments can lengthen the treatment time and affect the quality of the results.</p>
  </div>
  <div class="abs" style="left:17px;top:342px;width:160px">
    <div class="sec-head"><span class="num">11.</span><span class="sec-title">Co-operation</span></div>
    <p>Co-operation throughout treatment is your best guarantee of achieving a pleasing smile and good bite. Failure to co-operate could force the orthodontist to change the procedures and goals of your treatment. As a last resort treatment might have to be suspended. Consequences of early suspension may be worse than no treatment at all.</p>
  </div>
  <div class="abs" style="left:17px;top:451px;width:160px">
    <div class="sec-head"><span class="num">12.</span><span class="sec-title">General Health</span></div>
    <p>General medical problems can affect orthodontic treatment. You should keep your orthodontist informed of any changes to you medical health.</p>
  </div>
  <div class="abs" style="left:189px;top:28px;width:166px">
    <div class="sec-head"><span class="num">13.</span><span class="sec-title">Ceramic Brackets</span></div>
    <p>here ceramic brackets have been used, there have been some reported incidents of patients experiencing bracket breakage or damage to teeth, including the wearing down of tooth enamel and flaking or fracturing of the tooth's enamel on debanding. Fractured brackets may result in remnants which may be harmful to the patient especially if they are chewed on, swallowed or aspirated.</p>
  </div>
  <div class="abs" style="left:189px;top:143px;width:166px">
    <div class="sec-head"><span class="num">14.</span><span class="sec-title">Complementary<br>Aesthetic Dentistry</span></div>
    <p>If your teeth vary from normal in the number, size or shape of the teeth, achievement of the ideal result (for example, complete closure of exces sive space) may require restorative treatment. The most common types of complementary treatment are cosmetic bonding, crown and bridge restorative dental care and periodontal therapy.</p>
  </div>
  <div class="abs partner"><span class="partner-mark"></span><span>KEV</span></div>
  <div class="abs form">
    <div class="line-row"><span>I hereby authorize</span><span class="rule"></span></div>
    <p style="margin-top:6px;color:var(--ink);padding-left:2px">To carry out orthodontic treatment and any other related procedures deemed necessary including X-rays, for the welfare and treatment of:</p>
    <div class="full"></div>
    <div style="margin-top:12px">Signature of patient or parent/guardian</div>
    <div class="full" style="height:8px"></div>
    <div class="line-row" style="margin-top:6px;width:128px"><span>Name</span><span class="rule"></span></div>
    <div class="line-row"><span>Relationship to patient</span><span class="rule"></span></div>
    <div class="line-row" style="width:128px"><span>Date</span><span class="rule"></span><span>/</span><span class="rule"></span><span>/</span><span class="rule"></span></div>
    <div class="line-row"><span>Signature of Orthodontist</span><span class="rule"></span></div>
  </div>
</section>

<section class="page p5">
  <div class="wip">
    <div class="big">Page 5</div>
    <div class="wip-lines">The work is<br>inprogress<br>I will submit<br>in the next<br>12 - 15 hours</div>
  </div>
</section>

<section class="page p6">
  <div class="wip">
    <div class="big">Page 6</div>
    <div class="wip-lines">The work is<br>inprogress<br>I will submit<br>in the next<br>12 - 15 hours</div>
  </div>
</section>

</body>
</html>
```